Bluefern Business Services needs a new interactive and interesting website

We need an interesting, professional, modern and functional company website for Bluefern Business Services - a young IT Services company based out of Chennai, India.

Bluefern Business Services is a fully owned subsidiary of Marlow Goods, one of the world's leading direct to consumer wine merchant.

We already have a registered company logo which must feature in the website.

We conceive, design, develop, test, implement and support IT solutions across the entire Marlow Goods IT landscape. For ex : We currently run about 25 e-commerce websites for Marlow Goods on ATG and Dot Net.

We would like to see our corporate colors used in the website. (Burgundy wine and wine green - source: www.bluefernbs-site.com)

We are looking at this website to communicate a fun, friendly and professionally managed company - reaching out to career seekers, prospective customers and general public.

For reference - The company name 'Bluefern' is an inspiration from the Marlow Goods lineage.

The second image with the world map is stickered on our main entrance to the office, I am not sure where this can be used -just putting it out there..

Please note that there are only a few more days to submit designs for this contest  !

I would appreciate if you can help posting your designs in time for our review and consideration.

Thanks.

Reason: Thanks for your inputs. We have a number of designers and a lot to digest and work with in the past few days. There has been a rush of new designs in the last few days Hence we will require more time to process these and make our decision. Hence i am requesting the contest to be open for more days. Regards, Tarun

Target Market(s)

Prospective job seekers who want to know more about the company and also wish to apply for a job vacancy
People wanting to know more about the company in general and our progress
People who want to see what we offer and how we can help them too - prospective customers
Companies that are interested in our IT Captive journey and are looking for a business opportunity

Industry/Entity Type

E-Commerce

Requirements
Must have
• Log In/ Register facility acting as a Single Sign on for Intranet (Employees)

Facility to post job vacancies (with an expiry date) and enable people to apply for a role and upload their CV/Resume.

Facility to Review Job applications

Facility for website visitors to contact Bluefern business Services via an online 'Contact Us' form with a split of job seekers and business opportunities

Gallery facility to upload pictures regarding company events
Nice to have
• Less Cluttered and contemporary design
Some Wine/Vineyard inspirations will be good but not too much, the company is an IT services company

```html
<!DOCTYPE html>
<html lang="en">
<head>
<meta charset="utf-8">
<title>Bluefern Business Services</title>
<link href="https://fonts.googleapis.com/css2?family=Oswald:wght@400;500&family=Lato:ital,wght@0,400;0,700;1,400&display=swap" rel="stylesheet">
<style>
:root{
  --burgundy:#850040;
  --wine-green:#1e5a1e;
  --link-green:#1f5f22;
  --band:#efefef;
  --panel:#eeeeee;
  --text:#333333;
  --muted:#777777;
  --footer:#2f2f2f;
  --white:#ffffff;
}
*{box-sizing:border-box;margin:0;padding:0}
html,body{width:1200px;height:1097px;overflow:hidden}
body{position:relative;background:var(--white);font-family:'Lato',sans-serif;color:var(--text)}
.abs{position:absolute}
.site-header{left:0;top:0;width:1200px;height:92px;background:var(--burgundy);border-bottom:3px solid var(--wine-green)}
.brand{left:131px;top:12px;color:var(--white)}
.brand-row{display:flex;align-items:center;gap:8px}
.brand-mark{width:30px;height:30px;border-radius:50%;background:var(--white)}
.brand-name{font-weight:700;font-size:32px;line-height:32px}
.brand-sub{font-weight:400;font-size:22px;line-height:24px;margin-left:38px}
.main-nav{right:140px;top:53px;display:flex}
.main-nav a{font-family:'Oswald',sans-serif;font-size:17px;color:var(--white);text-decoration:none;padding:0 10px;margin-left:10px;height:27px;line-height:27px}
.main-nav a.active{background:var(--white);color:var(--wine-green)}
.hero-band{left:0;top:92px;width:1200px;height:341px;background:var(--band)}
.hero{left:130px;top:107px;width:941px;height:306px;border:1px solid #555;background:linear-gradient(90deg,#4f5b60 0%,#66757a 45%,#8a9196 62%,#3a3f42 100%)}
.hero-title{left:25px;top:62px;font-family:'Oswald',sans-serif;font-size:32px;color:var(--white);font-weight:400}
.hero-text{left:24px;top:131px;width:340px;font-size:15px;line-height:22.5px;color:var(--white)}
.hero-btn{left:25px;top:209px;background:var(--burgundy);color:var(--white);font-size:11.5px;padding:4px 9px}
.arrow{font-family:'Oswald',sans-serif;font-size:34px;color:#888;top:224px}
.section-title{font-family:'Oswald',sans-serif;font-size:19px;color:#222;font-weight:400}
.section-title::after{content:"";display:block;width:84px;height:3px;background:var(--burgundy);margin-top:5px}
.copy{font-size:12.2px;line-height:18.75px;color:var(--text)}
.more{font-size:11.5px;color:var(--link-green)}
.btn-green{background:var(--wine-green);color:var(--white);font-size:11.5px;padding:2px 8px}
.clients-box{left:128px;top:657px;width:658px;height:119px;background:var(--panel)}
.client{top:12px;width:141px;height:94px;background:var(--white);display:flex;align-items:center;justify-content:center;text-align:center;font-weight:700;font-size:15px;color:var(--burgundy);padding:0 8px}
.event-img{top:828px;width:199px;height:121px}
.event-title{top:953px;font-size:12.2px;font-weight:700;color:#555}
.jobs{left:822px;top:486px;width:249px;height:290px;background:var(--panel)}
.job{left:12px;width:228px}
.job-date{font-style:italic;font-size:13.5px;color:var(--muted);padding-left:27px;position:relative}
.job-date::before{content:"›";position:absolute;left:0;top:1px;width:15px;height:15px;border:1px solid #999;border-radius:50%;font-size:13px;line-height:12px;text-align:center;color:#333;font-style:normal;background:#fafafa}
.job-role{font-size:12.2px;font-weight:700;line-height:17px;padding-left:24px;margin-top:4px;color:#333}
.job .more{display:block;text-align:right;margin-top:3px}
.video{left:823px;top:796px;width:247px;height:176px;background:radial-gradient(ellipse at 50% 45%,#4a3fa8 0%,#1d2a7a 45%,#0a0e2e 80%);border-bottom:22px solid #050505}
.landscape{left:0;top:930px;width:1200px;height:118px;background:linear-gradient(180deg,rgba(255,255,255,0) 0%,#efe8d6 45%,#c9c3a3 100%)}
.site-footer{left:0;top:1048px;width:1200px;height:49px;background:var(--footer);color:var(--white);font-size:11.5px}
.social{top:8px;width:34px;height:34px;border-radius:50%;background:#555}
</style>
</head>
<body>
<header class="site-header abs">
  <div class="brand abs">
    <div class="brand-row"><span class="brand-mark"></span><span class="brand-name">bluefern</span></div>
    <div class="brand-sub">Business Services</div>
  </div>
  <nav class="main-nav abs">
    <a class="active">Home</a><a>About Us</a><a>Client</a><a>Services</a><a>Careers</a><a>Contact Us</a>
  </nav>
</header>

<div class="hero-band abs"></div>
<span class="arrow abs" style="left:100px">❮</span>
<span class="arrow abs" style="left:1082px">❯</span>
<section class="hero abs" role="img" aria-label="Portrait photo of an executive in a suit">
  <h1 class="hero-title abs">Executive Team</h1>
  <p class="hero-text abs">Bluefern's executive team thrive on implementing and supporting cutting-edge solutions.Harnessing the ever-changing world of technology</p>
  <span class="hero-btn abs">Read More</span>
</section>

<div class="landscape abs" role="img" aria-label="Soft vineyard landscape"></div>

<section class="abs" style="left:130px;top:451px;width:305px">
  <h2 class="section-title">Welcome To Bluefern</h2>
  <p class="copy" style="margin-top:12px">Welcome to Bluefern Business Services, an emerging provider of global IT consulting and software services. We are part of the Marlow Goods group, a family run business and the world's largest multi-channel home de</p>
  <div class="more" style="text-align:right;margin-top:9px;width:290px">Read More</div>
</section>

<section class="abs" style="left:494px;top:451px;width:290px">
  <h2 class="section-title">Services</h2>
  <p class="copy" style="margin-top:12px">The services we provide enable the businesses we support to efficiently manage key functions, including order management (encompassing e-commerce websites, inbound and outbound call centre</p>
  <div class="more" style="text-align:right;margin-top:9px">Read More</div>
</section>

<h2 class="section-title abs" style="left:130px;top:622px">Clients</h2>
<span class="btn-green abs" style="left:727px;top:626px">View All</span>
<div class="clients-box abs">
  <div class="client abs" style="left:13px">Vesper Cellars</div>
  <div class="client abs" style="left:177px">Ledger Wine Club</div>
  <div class="client abs" style="left:341px;color:var(--wine-green)">Ashby Vintners</div>
  <div class="client abs" style="left:505px">Marlow Goods</div>
</div>

<h2 class="section-title abs" style="left:130px;top:792px">Events</h2>
<div class="event-img abs" style="left:129px;background:linear-gradient(180deg,#2c4a2a,#5a5a4a 55%,#c9c2bd)" role="img" aria-label="Event photo of a crowded hall"></div>
<div class="event-img abs" style="left:363px;background:linear-gradient(180deg,#1a1f5a,#7a3a8a 50%,#2a2540)" role="img" aria-label="Event photo of an award stage"></div>
<div class="event-img abs" style="left:595px;background:linear-gradient(180deg,#c9a24a,#8a6a3a 50%,#b07a6a)" role="img" aria-label="Event photo of a dinner in a marquee"></div>
<div class="event-title abs" style="left:129px">Event title goes here</div>
<div class="event-title abs" style="left:363px">Event title goes here</div>
<div class="event-title abs" style="left:595px">Event title goes here</div>

<h2 class="section-title abs" style="left:822px;top:452px">Latest Opportunities</h2>
<aside class="jobs abs">
  <div class="job abs" style="top:11px"><div class="job-date">26/11/2013</div><div class="job-role">Software Developers/Programmer Analysts - AX</div><span class="more">Read More</span></div>
  <div class="job abs" style="top:95px"><div class="job-date">26/11/2013</div><div class="job-role">Software Developers/Programmer Analysts - AX</div><span class="more">Read More</span></div>
  <div class="job abs" style="top:180px"><div class="job-date">26/11/2013</div><div class="job-role">Software Developers/Programmer Analysts - AX</div><span class="more">Read More</span></div>
  <span class="btn-green abs" style="left:19px;top:253px">View All</span>
</aside>

<div class="video abs" role="img" aria-label="Video thumbnail with glowing light rings">
  <svg class="abs" style="left:104px;top:70px" width="38" height="38" viewBox="0 0 38 38"><circle cx="19" cy="19" r="17" fill="rgba(255,255,255,.25)" stroke="#fff" stroke-width="3"/><path d="M15 11 L27 19 L15 27Z" fill="#fff"/></svg>
</div>

<footer class="site-footer abs">
  <span class="abs" style="left:131px;top:18px">Copyright Bluefern Business Services Private Limited.</span>
  <span class="social abs" style="left:992px" aria-label="Social link one"></span>
  <span class="social abs" style="left:1035px" aria-label="Social link two"></span>
</footer>
</body>
</html>
```